Lone Star Wetland Flora Stewardship Guild

We need to design the home page of this new website. We would like a fun website design for provides as a resource for members and information for potential members.
Please design so that we can see a portion of background on each side on the website.
I just need the final design files psd no coding needed.
Attached is their logo (colors are not 100% set in stone either so can mess with those as I did in the quick mockup attached)
Attached is a pdf newsletter they send out, you can get a feel for them and what they are about. The design is crappy and we are here to fix that going forward and we are starting with the website.
Here are some quick example websites (design style is open)
- I attached a quick mockup i did just for a content visual but by all means do what you want.
- http://www.brightpathleaders.example/
- http://www.civicunityhub.example/
- http://preview.webskinvault.example/show.php?cat=layouts&host=skinbazaar&temp=novaline
- http://www.meadowkeep.example/
- http://www.urbangleaners.example/
- http://www.projectcozyknit.example/
here are some of the other chapters website (pretty bad!)
and here are some of the others:
- http://www.dwrvcs.example/
- http://kwfg.example/
- http://www.blvcg.example/
Content Items that need to be included:
1. Logo
2. Menu - home, about, members, resources, events, membership, contact
3. Become a member - button or action
4. social links - chatterloop, workweave, clipstream
5. banner - that needs to explain their purpose "Promoting environmental stewardship through operations, research, education and outreach" (or this can be worked into the design)
6. Upcoming event (s)
7. Advertisement - members can place an ad on the website, this can be a placeholder for now
8. newsletter signup
9. advertise with us - this link can be in the footer
30-60 years of age, succesfull (household budgets of 120K+ men and women that live in texas.
Education

```html
<!DOCTYPE html>
<html lang="en">
<head>
<meta charset="utf-8">
<title>Lone Star Wetland Flora Stewardship Guild — Home</title>
<link href="https://fonts.googleapis.com/css2?family=Open+Sans:wght@400;600;700&family=Arimo:wght@400&display=swap" rel="stylesheet">
<style>
  :root{
    --navy:#0b3c8c;
    --red:#d9475a;
    --ink:#333333;
    --muted:#666666;
    --panel:#ebebeb;
    --backdrop-dark:#1d1f1e;
    --white:#ffffff;
    --social-chatterloop:#2c4a8f;
    --social-clipstream:#b0261f;
    --social-workweave:#0e6ea8;
  }
  *{box-sizing:border-box;margin:0;padding:0}
  html,body{width:1000px;height:1200px;overflow:hidden}
  body{position:relative;font-family:"Open Sans",sans-serif;color:var(--ink);background:var(--backdrop-dark)}
  .abs{position:absolute}
  .backdrop-lake{left:0;top:0;width:1000px;height:560px;
    background:linear-gradient(180deg,#4d6b68 0%,#3f5f58 40%,#2d3f38 75%,var(--backdrop-dark) 100%)}
  .page{left:85px;top:35px;width:830px;height:900px;background:var(--white);border-top:2px solid var(--navy)}

  .brand{left:101px;top:56px;width:220px}
  .brand-row{display:flex;align-items:center;gap:9px}
  .brand-mark{width:20px;height:20px;background:var(--red)}
  .brand-name{font-size:36px;font-weight:700;color:var(--navy);letter-spacing:1px;line-height:1}
  .brand-full{margin-top:12px;font-size:7.4px;font-weight:700;color:#111;white-space:nowrap}

  .utility{top:63px;font-size:12px;color:#444;display:flex;align-items:center;gap:5px}
  .social-links{left:598px;top:60px;display:flex;flex-direction:column;gap:1px}
  .social{display:flex;align-items:center;gap:4px;font-size:8.5px;font-weight:600;color:#444;line-height:8px;text-decoration:none}
  .social i{width:7px;height:7px;display:block}
  .social.chatterloop i{background:var(--social-chatterloop)}
  .social.clipstream i{background:var(--social-clipstream)}
  .social.workweave i{background:var(--social-workweave)}
  .btn-join{left:753px;top:60px;width:146px;height:25px;background:var(--red);color:var(--white);
    border-radius:3px;font-size:12px;font-weight:600;display:flex;align-items:center;justify-content:center;
    box-shadow:0 2px 3px rgba(0,0,0,.25)}

  .main-nav{left:101px;top:120px;width:799px;height:29px;border-bottom:2px solid var(--navy)}
  .main-nav a{position:absolute;top:0;height:27px;line-height:27px;font-size:13px;color:#555;text-decoration:none;transform:translateX(-50%);white-space:nowrap}
  .main-nav a.active{background:var(--navy);color:var(--white);width:73px;text-align:center;border-radius:3px 3px 0 0;font-weight:600}

  .hero{left:101px;top:150px;width:798px;height:391px;
    background:linear-gradient(180deg,#a9cbe6 0%,#d6e6f1 22%,#5d8a3e 38%,#6b8f74 55%,#8ea06a 75%,#b7b857 100%)}
  .hero-arrow{top:322px;width:37px;height:37px;background:rgba(255,255,255,.45);display:flex;align-items:center;justify-content:center}
  .hero-tag{left:147px;top:387px;width:122px;height:35px;background:rgba(36,78,140,.85);color:var(--white);
    font-size:19px;display:flex;align-items:center;justify-content:center}
  .hero-caption{left:147px;top:433px;width:483px;height:60px;background:rgba(30,30,30,.75);color:var(--white);
    font-size:15.5px;font-weight:600;line-height:20px;padding:10px 0 0 16px}
  .dots{top:546px;left:488px;display:flex;gap:6px}
  .dots span{width:5px;height:5px;border-radius:50%;background:#d6d6d6}
  .dots span.on{background:var(--red)}

  .section-title{font-size:21px;font-weight:400;color:#333}
  .about-img{left:100px;top:610px;width:252px;height:124px;background:linear-gradient(180deg,#b9cde0 0%,#8ab35e 40%,#6b8a6a 70%,#4d6b44 100%)}
  .about-text{left:101px;top:749px;width:252px;font-size:10.8px;line-height:15px;text-align:justify;text-align-last:center;color:#333}
  .btn-read{left:170px;top:834px;width:94px;height:20px;background:var(--navy);color:var(--white);border-radius:3px;font-size:10.5px;display:flex;align-items:center;justify-content:center}

  .event-img{left:382px;width:91px;height:64px}
  .event-title{left:486px;font-size:12.5px;color:#222}
  .event-date{left:486px;font-size:9px;color:#333}
  .event-date b{font-weight:600}
  .event-text{left:486px;width:143px;font-size:9.8px;line-height:12.5px;color:#555;text-align:justify}

  .ads{left:670px;top:568px;width:226px;height:230px;background:#f2f2f2}
  .ad-tile{width:104px;height:104px;overflow:hidden;display:flex;flex-direction:column;color:var(--white)}
  .ad-free{left:672px;top:571px;background:#e96a78;align-items:center;justify-content:center;font-size:13px;letter-spacing:.5px}
  .ad-design{left:790px;top:571px;background:#2fd42a;align-items:center;justify-content:center;line-height:1}
  .ad-design .big{font-size:26px;font-weight:400;letter-spacing:-.5px;color:#f4f4f4;text-shadow:0 0 0 transparent}
  .ad-design .small{font-size:8px;margin:2px 0;color:#f4f4f4}
  .ad-design .inner{background:#1d1d1d;width:70px;height:104px;display:flex;flex-direction:column;align-items:center;justify-content:center}
  .ad-cube{left:672px;top:689px;background:linear-gradient(160deg,#2a2a2a 55%,#1f6f8a);justify-content:flex-end;align-items:center;padding-bottom:10px}
  .ad-cube .name{font-size:15px;font-weight:700;letter-spacing:.5px}
  .ad-cube .sub{font-size:6.5px;font-weight:700;color:#cfcfcf}
  .ad-stock{left:790px;top:689px;background:linear-gradient(180deg,#3b9a2e 0 26px,#1e3a1c 26px);padding:6px 8px;font-size:11px}
  .ad-stock .name{font-size:11px;font-weight:600;margin-bottom:12px}
  .ad-stock .line{font-size:10.5px;font-weight:700;line-height:14px}
  .ad-stock .cta{margin-top:8px;background:#3b9a2e;font-size:8px;padding:1px 4px;align-self:flex-start}
  .ad-slot{left:673px;top:817px;width:226px;height:42px;background:#d9d9d9;font-size:12.5px;color:#333;display:flex;align-items:center;justify-content:center}

  .footer{left:85px;top:935px;width:830px;height:203px;background:var(--panel);border-top:1px solid #dcdcdc}
  .foot-h{top:963px;font-size:12px;font-weight:600;color:#222;letter-spacing:.2px}
  .foot-links{left:103px;top:997px;list-style:none;font-size:10.5px;color:#666;line-height:20.5px}
  .foot-contact{left:312px;font-size:10.5px;color:#666;line-height:14px;display:flex;gap:6px}
  .foot-contact svg{flex:none;margin-top:2px}
  .advertise-box{left:539px;top:965px;width:150px;height:133px;background:var(--red);color:var(--white);border-radius:2px;
    font-size:19px;letter-spacing:2px;line-height:24px;display:flex;align-items:center;justify-content:center;text-align:center}
  .field{left:749px;width:149px;height:26px;border:1px solid #cfcfcf;background:#f2f2f2;font-size:10px;color:#aaa;padding:6px 0 0 12px}
  .btn-sub{left:749px;top:1085px;width:149px;height:26px;background:var(--navy);color:var(--white);font-size:10.5px;font-weight:600;display:flex;align-items:center;justify-content:center}

  .legal{left:85px;top:1138px;width:830px;height:41px;background:var(--navy);color:var(--white);
    font-family:"Arimo",sans-serif;font-size:10px;display:flex;align-items:center;justify-content:center;gap:6px}
</style>
</head>
<body>
  <div class="abs backdrop-lake" role="img" aria-label="Lake with water lilies and reeds, behind the page"></div>
  <div class="abs page"></div>

  <header>
    <div class="abs brand">
      <div class="brand-row"><span class="brand-mark"></span><span class="brand-name">LSWFSG</span></div>
      <div class="brand-full">Lone Star Wetland Flora Stewardship Guild</div>
    </div>

    <div class="abs utility" style="left:460px">
      <svg width="9" height="12" viewBox="0 0 9 12"><path d="M2 0h2l1 3-1.5 1c.6 1.6 1.6 2.8 3 3.5L8 6l1 2v2c-4 1-9-4-8-9z" fill="#333"/></svg>Contact
    </div>
    <div class="abs utility" style="left:530px">
      <svg width="12" height="12" viewBox="0 0 12 12"><path d="M5 1h6v10H5" fill="none" stroke="#333" stroke-width="1.3"/><path d="M1 6h6M5 4l2 2-2 2" fill="none" stroke="#333" stroke-width="1.3"/></svg>Login
    </div>
    <div class="abs social-links">
      <a class="social chatterloop"><i></i>chatterloop</a>
      <a class="social clipstream"><i></i>clipstream</a>
      <a class="social workweave"><i></i>workweave</a>
    </div>
    <div class="abs btn-join">Become a member</div>

    <nav class="abs main-nav">
      <a class="active" style="left:301px">Home</a>
      <a style="left:366px">About</a>
      <a style="left:441px">Members</a>
      <a style="left:526px">Resources</a>
      <a style="left:604px">Events</a>
      <a style="left:689px">Membership</a>
      <a style="left:776px">Contact</a>
    </nav>
  </header>

  <section>
    <div class="abs hero" role="img" aria-label="Pond covered with lily pads under a blue sky, trees on the far bank"></div>
    <div class="abs hero-arrow" style="left:120px"><svg width="10" height="14"><path d="M8 1L2 7l6 6" fill="none" stroke="#777" stroke-width="2"/></svg></div>
    <div class="abs hero-arrow" style="left:845px"><svg width="10" height="14"><path d="M2 1l6 6-6 6" fill="none" stroke="#777" stroke-width="2"/></svg></div>
    <div class="abs hero-tag">LSWFSG</div>
    <div class="abs hero-caption">Promoting Environmental Stewardship Through operations,<br>Research, Education and Outreach</div>
    <div class="abs dots"><span class="on"></span><span></span><span></span></div>
  </section>

  <section>
    <h2 class="abs section-title" style="left:101px;top:568px">About Us</h2>
    <div class="abs about-img" role="img" aria-label="Reeds along a calm pond"></div>
    <p class="abs about-text">Lorem ipsum dolor sit amet, consectetur dipiscing elit. Suspendisse nec dolor bibendum, placerat eros id, rutrum ligula. Aliquam eget convallis erat. In consequat purus lacus,</p>
    <div class="abs btn-read">Read More</div>
  </section>

  <section>
    <h2 class="abs section-title" style="left:382px;top:568px">Upcoming event’s</h2>
    <svg class="abs" style="left:601px;top:573px" width="28" height="16"><path d="M8 2L2 8l6 6" fill="none" stroke="#999" stroke-width="2"/><path d="M19 2l6 6-6 6" fill="none" stroke="var(--navy)" stroke-width="2.2"/></svg>

    <div class="abs event-img" style="top:611px;background:linear-gradient(135deg,#2f4a2a,#5a7a3a,#22331d)" role="img" aria-label="Lily pads on dark water"></div>
    <div class="abs event-title" style="top:606px">Fusce quis erat</div>
    <div class="abs event-date" style="top:624px">19-05-2014 &nbsp;| &nbsp;<b>Monday</b></div>
    <p class="abs event-text" style="top:641px">at massa unt porta. Nulla vel placerat lus. Donec a libero non elit avida posuere.</p>

    <div class="abs event-img" style="top:703px;background:linear-gradient(135deg,#6d8a3a,#8a7bb8,#3c5a25)" role="img" aria-label="Purple water lily flowers"></div>
    <div class="abs event-title" style="top:698px">Fusce quis erat</div>
    <div class="abs event-date" style="top:716px">19-05-2014 &nbsp;| &nbsp;<b>Monday</b></div>
    <p class="abs event-text" style="top:733px">at massa unt porta. Nulla vel placerat lus. Donec a libero non elit avida posuere.</p>

    <div class="abs event-img" style="top:794px;background:linear-gradient(135deg,#4a3a1e,#6e8a2e,#2e2a18)" role="img" aria-label="Green aquatic grass in shallow water"></div>
    <div class="abs event-title" style="top:790px">Fusce quis erat</div>
    <div class="abs event-date" style="top:807px">19-05-2014 &nbsp;| &nbsp;<b>Monday</b></div>
    <p class="abs event-text" style="top:824px">at massa unt porta. Nulla vel placerat lus. Donec a libero non elit avida posuere.</p>
  </section>

  <aside>
    <div class="abs ads"></div>
    <div class="abs ad-tile ad-free" role="img" aria-label="Sponsor ad with a seated silhouette">FreeShapes</div>
    <div class="abs ad-tile ad-design" role="img" aria-label="Web design sponsor ad">
      <div class="inner"><span class="big">DESIGN</span><span class="small">your</span><span class="big">WEBSITE</span></div>
    </div>
    <div class="abs ad-tile ad-cube" role="img" aria-label="Website builder sponsor ad">
      <span class="name">CUBEFORGE</span><span class="sub">CREATE FLASH WEBSITES</span>
    </div>
    <div class="abs ad-tile ad-stock" role="img" aria-label="Stock image sponsor ad">
      <span class="name">stockmeadow</span>
      <span class="line">Any image.</span><span class="line">One price.</span>
      <span class="cta">Learn More</span>
    </div>
    <div class="abs ad-slot">Advertise Here</div>
  </aside>

  <footer>
    <div class="abs footer"></div>
    <h3 class="abs foot-h" style="left:104px">IN BRIEF</h3>
    <ul class="abs foot-links">
      <li>Site map</li><li>About Us</li><li>Success stories</li><li>Becoming a solution partner</li>
    </ul>

    <h3 class="abs foot-h" style="left:310px">CONTACT</h3>
    <div class="abs foot-contact" style="top:997px">
      <svg width="7" height="10" viewBox="0 0 7 10"><path d="M3.5 0A3.5 3.5 0 0 0 0 3.5C0 6 3.5 10 3.5 10S7 6 7 3.5A3.5 3.5 0 0 0 3.5 0z" fill="#888"/><circle cx="3.5" cy="3.5" r="1.3" fill="#ebebeb"/></svg>
      <span>218 Marsh Hollow Lane Suite 4-B<br>Cedar Bend, TX 75400</span>
    </div>
    <div class="abs foot-contact" style="top:1040px">
      <svg width="8" height="9" viewBox="0 0 9 12"><path d="M2 0h2l1 3-1.5 1c.6 1.6 1.6 2.8 3 3.5L8 6l1 2v2c-4 1-9-4-8-9z" fill="#888"/></svg>
      <span>(555) 310-2874, (555) 310-6619</span>
    </div>
    <div class="abs foot-contact" style="top:1070px">
      <svg width="8" height="8" viewBox="0 0 8 6"><rect width="8" height="6" fill="#888"/><path d="M0 0l4 3 4-3" fill="none" stroke="#ebebeb" stroke-width=".8"/></svg>
      <span>Email: info@wetlandguild.example</span>
    </div>

    <div class="abs advertise-box">ADVERTISE<br>WITH US</div>

    <h3 class="abs foot-h" style="left:746px">NEWSLETTER SIGNUP</h3>
    <div class="abs field" style="top:997px">Name</div>
    <div class="abs field" style="top:1032px">Email id</div>
    <div class="abs btn-sub">Subscribe now</div>

    <div class="abs legal">
      <span>Copyright © yourwebsite</span><span>|</span><span>Terms &amp; Conditions</span><span>|</span><span>Privacy Policy</span><span>|</span><span>Cookies Policy</span><span>|</span><span>Contact us</span>
    </div>
  </footer>
</body>
</html>
```